Tall Fern Roofing Business Card

Need a business card with the logo that was designed here

Contact Information for Business Card

Name, Title, Phone, Email, Website, Company name

```html
<!DOCTYPE html>
<html lang="en">
<head>
<meta charset="utf-8">
<title>Tall Fern Roofing Business Card</title>
<link href="https://fonts.googleapis.com/css2?family=Open+Sans:wght@400;600;700&display=swap" rel="stylesheet">
<style>
  :root {
    --page: #232323;
    --card: #1e1e22;
    --card-back: #1a1a1d;
    --blue: #1273bf;
    --grey: #8e8f93;
    --white: #f2f2f2;
    --rule: #9a9a9a;
    --emboss: #121214;
  }
  * { margin: 0; padding: 0; box-sizing: border-box; }
  html, body { width: 1200px; height: 780px; overflow: hidden; background: var(--page); }
  body { font-family: "Open Sans", Arial, sans-serif; position: relative; }

  .card {
    position: absolute;
    width: 540px;
    height: 310px;
    border-radius: 3px;
    box-shadow: 0 18px 40px rgba(0,0,0,.55);
    overflow: hidden;
  }
  .card-front { left: 45px; top: 235px; background: var(--card); }
  .card-back { left: 615px; top: 235px; background: var(--card-back); }

  .brand {
    position: absolute;
    left: 38px; top: 78px;
    width: 190px;
    color: var(--blue);
    font-weight: 700;
    font-size: 28px;
    line-height: 1.1;
    display: flex; align-items: center; gap: 10px;
  }
  .brand-dot { width: 12px; height: 12px; background: var(--blue); flex: none; }

  .divider {
    position: absolute;
    left: 250px; top: 40px;
    width: 1px; height: 170px;
    background: var(--rule);
  }

  .person { position: absolute; left: 272px; top: 48px; }
  .person-name { font-size: 30px; font-weight: 700; line-height: 1.05; color: var(--grey); }
  .person-name .first { color: var(--blue); }
  .person-title { font-size: 14px; color: var(--white); margin-top: 2px; }

  .contacts { list-style: none; margin-top: 14px; }
  .contacts li {
    display: flex; align-items: center; gap: 8px;
    font-size: 13px; color: var(--white); line-height: 22px;
  }
  .contacts svg { width: 13px; height: 13px; flex: none; }

  .address-band {
    position: absolute;
    left: 0; top: 256px;
    width: 440px; height: 32px;
    background: var(--blue);
    clip-path: polygon(0 0, 100% 0, 96% 100%, 0 100%);
    color: var(--white);
    font-size: 14px;
    line-height: 32px;
    padding-left: 34px;
  }

  .back-brand {
    position: absolute; inset: 0;
    display: flex; align-items: center; justify-content: center; gap: 14px;
    color: var(--emboss);
    font-size: 40px; font-weight: 700;
    text-shadow: none;
  }
  .back-brand .brand-dot { width: 16px; height: 16px; background: var(--emboss); }
</style>
</head>
<body>
  <section class="card card-front">
    <div class="brand"><span class="brand-dot"></span><span>Tall Fern Roofing</span></div>
    <div class="divider"></div>
    <div class="person">
      <h1 class="person-name"><span class="first">Dale</span> Harwick</h1>
      <p class="person-title">Owner</p>
      <ul class="contacts">
        <li>
          <svg viewBox="0 0 24 24" aria-hidden="true"><path fill="#1273bf" d="M6.6 10.8a15 15 0 0 0 6.6 6.6l2.2-2.2a1 1 0 0 1 1-.25 11.4 11.4 0 0 0 3.6.57 1 1 0 0 1 1 1V20a1 1 0 0 1-1 1A17 17 0 0 1 3 4a1 1 0 0 1 1-1h3.5a1 1 0 0 1 1 1c0 1.25.2 2.45.57 3.57a1 1 0 0 1-.25 1z"/></svg>
          555-210-4837
        </li>
        <li>
          <svg viewBox="0 0 24 24" aria-hidden="true"><circle cx="12" cy="12" r="9" fill="none" stroke="#1273bf" stroke-width="2.5"/><path d="M3 12h18M12 3c3 3 3 15 0 18M12 3c-3 3-3 15 0 18" fill="none" stroke="#1273bf" stroke-width="1.8"/></svg>
          www.tallfernroofing.com
        </li>
        <li>
          <svg viewBox="0 0 24 24" aria-hidden="true"><rect x="2" y="5" width="20" height="14" rx="2" fill="#1273bf"/><path d="M3 6l9 7 9-7" fill="none" stroke="#1e1e22" stroke-width="2"/></svg>
          dale@tallfernroofing.com
        </li>
      </ul>
    </div>
    <div class="address-band">PO Box 118 Millbrook, PA 16500</div>
  </section>

  <section class="card card-back">
    <div class="back-brand"><span class="brand-dot"></span><span>Tall Fern Roofing</span></div>
  </section>
</body>
</html>
```